Carpet cleaning company focused on high quality needs business cards

We are a growing company that just merged with another company and need to design a new business card. We do both residential as well as commercial cleaning. We do carpet, tile & grout, upholstery, hard floors, and stain & pet odor removal. We treat our customers like family and strive to achieve outstanding results with every job.

```html
<!DOCTYPE html>
<html lang="en">
<head>
<meta charset="utf-8">
<title>Harbor Steam Crew – Business Card</title>
<link rel="stylesheet" href="https://fonts.googleapis.com/css2?family=Montserrat:wght@400;500;600;800&display=swap">
<style>
  :root {
    --stage: #e4e4e7;
    --card-dark: #2f2f33;
    --card-light: #ffffff;
    --brand-red: #e8413b;
    --ink: #1c1c1f;
    --ink-soft: #2b2b2e;
    --white: #ffffff;
  }
  * { box-sizing: border-box; margin: 0; padding: 0; }
  html, body {
    width: 1200px; height: 900px; overflow: hidden;
    background: var(--stage);
    font-family: "Montserrat", sans-serif;
  }
  .stage {
    width: 1200px; height: 900px;
    display: flex; flex-direction: column;
    align-items: center; justify-content: center; gap: 48px;
  }
  .card {
    width: 620px; height: 354px; border-radius: 24px;
    position: relative; overflow: hidden;
    box-shadow: 0 10px 30px rgba(0,0,0,.18);
  }
  /* Front */
  .card--front {
    background: var(--card-dark);
    display: flex; align-items: center; justify-content: center;
  }
  .brand { display: flex; align-items: center; gap: 18px; }
  .brand__mark { background: var(--brand-red); flex: none; }
  .brand__name {
    font-weight: 800; text-transform: uppercase; line-height: 1.02;
    letter-spacing: .01em;
  }
  .card--front .brand__mark { width: 96px; height: 96px; }
  .card--front .brand__name { color: var(--white); font-size: 34px; }

  /* Back */
  .card--back { background: var(--card-light); }
  .card--back .brand {
    position: absolute; left: 188px; top: 46px; gap: 14px;
  }
  .card--back .brand__mark { width: 62px; height: 62px; }
  .card--back .brand__name { color: var(--ink); font-size: 22px; }

  .details {
    position: absolute; left: 0; right: 0; top: 150px;
    display: flex; justify-content: center; align-items: stretch; gap: 22px;
  }
  .person { text-align: right; color: var(--ink-soft); }
  .person__name {
    color: var(--brand-red); font-weight: 600; font-size: 27px; line-height: 1.1;
  }
  .person__role { font-size: 14px; margin-top: 2px; }
  .person__address { font-size: 13px; line-height: 1.35; margin-top: 12px; }
  .divider { width: 1.5px; background: var(--brand-red); }
  .contact { list-style: none; color: var(--ink-soft); font-size: 13px; }
  .contact li { display: flex; align-items: center; gap: 10px; line-height: 1; margin-bottom: 10px; }
  .contact svg { width: 14px; height: 14px; flex: none; fill: var(--brand-red); }
  .license {
    position: absolute; left: 0; right: 0; bottom: 48px;
    text-align: center; color: var(--brand-red); font-size: 14px; font-weight: 500;
  }
</style>
</head>
<body>
<main class="stage">
  <section class="card card--front" aria-label="Card front">
    <div class="brand">
      <span class="brand__mark"></span>
      <span class="brand__name">Harbor<br>Steam Crew</span>
    </div>
  </section>

  <section class="card card--back" aria-label="Card back">
    <div class="brand">
      <span class="brand__mark"></span>
      <span class="brand__name">Harbor<br>Steam Crew</span>
    </div>

    <div class="details">
      <div class="person">
        <p class="person__name">Daniel Reyes</p>
        <p class="person__role">CEO</p>
        <p class="person__address">418 Maple Grove Ave, #112<br>Fairview, OH 45010</p>
      </div>
      <span class="divider"></span>
      <ul class="contact">
        <li>
          <svg viewBox="0 0 16 16" aria-hidden="true"><path d="M2 5c0-1.5 2-3 6-3s6 1.5 6 3v1h-3V5H5v1H2zM4 7h8l2 6H2z"/></svg>
          555 010-4821
        </li>
        <li>
          <svg viewBox="0 0 16 16" aria-hidden="true"><path d="M4 1h8v14H4zM5.5 2.5v9.5h5V2.5z"/></svg>
          555 010-4821
        </li>
        <li>
          <svg viewBox="0 0 16 16" aria-hidden="true"><path d="M1 3h14v10H1zM2.5 4.5 8 9l5.5-4.5z"/></svg>
          info@harborsteamcrew.com
        </li>
        <li>
          <svg viewBox="0 0 16 16" aria-hidden="true"><path d="M8 1a7 7 0 1 0 0 14A7 7 0 0 0 8 1zm0 1.5c.9 1 1.5 3 1.6 4.7H6.4C6.5 5.5 7.1 3.5 8 2.5zM2.6 8.8h2.3c.1 1.7.5 3.2 1.1 4.3A5.5 5.5 0 0 1 2.6 8.8zm0-1.6A5.5 5.5 0 0 1 6 2.9C5.4 4 5 5.5 4.9 7.2zm3.8 1.6h3.2c-.1 1.7-.7 3.7-1.6 4.7-.9-1-1.5-3-1.6-4.7zm4.7 0h2.3a5.5 5.5 0 0 1-3.4 4.3c.6-1.1 1-2.6 1.1-4.3zm0-1.6c-.1-1.7-.5-3.2-1.1-4.3a5.5 5.5 0 0 1 3.4 4.3z"/></svg>
          www.harborsteamcrew.com
        </li>
      </ul>
    </div>

    <p class="license">License Number #0987654</p>
  </section>
</main>
</body>
</html>
```